TalkHarbor - Language Coaching Services

Sleek, innovative, trendy design for Language Coaching business.

TalkHarbor is a new UK based company that provides Language Coaching services. We offer highly personalized on-line and face to face language courses. We also impart learning techniques workshops based on the latest neuroscience research for second-language acquisition.

Target Market(s)

See attached info

Industry/Entity Type

Consulting

Contact Information for Business Card

TalkHarbor
DaniaKV@talkharbor.co.uk
TalkHarbor.co.uk
London, UK

Font styles to use
Sans Serif

```html
<!DOCTYPE html>
<html lang="en">
<head>
<meta charset="utf-8">
<title>TalkHarbor Business Card</title>
<link rel="stylesheet" href="https://fonts.googleapis.com/css2?family=Lato:wght@400;700&family=Montserrat:wght@600&display=swap">
<style>
  :root {
    --page-bg: #2a2a2c;
    --card-bg: #1c1c1e;
    --card-edge: #2c2c2f;
    --brand-blue: #1b8fc4;
    --silver: #d4d4d6;
    --text-light: #f2f2f2;
    --rule: #3a3a3e;
  }
  * { box-sizing: border-box; margin: 0; padding: 0; }
  html, body {
    width: 1200px; height: 900px; overflow: hidden;
    background: var(--page-bg);
    font-family: "Lato", Arial, sans-serif;
  }
  .stage {
    width: 1200px; height: 900px;
    display: flex; flex-direction: column; align-items: center; justify-content: center;
    gap: 40px;
  }
  .card {
    position: relative;
    width: 700px; height: 400px;
    background: var(--card-bg);
    border: 1px solid var(--card-edge);
    border-radius: 22px;
    box-shadow: 0 14px 30px rgba(0,0,0,0.45);
    overflow: hidden;
  }
  /* Back side */
  .card-back .brand-mark {
    position: absolute; left: 0; right: 0; top: 120px;
    display: flex; align-items: center; justify-content: center; gap: 18px;
  }
  .brand-dot {
    width: 64px; height: 64px; border-radius: 50%;
    border: 6px solid currentColor;
  }
  .card-back .brand-mark { color: var(--silver); }
  .brand-name {
    font-family: "Lato", Arial, sans-serif;
    font-weight: 700; font-size: 40px; letter-spacing: 1px;
  }
  .card-back .site {
    position: absolute; left: 0; right: 0; bottom: 70px;
    text-align: center; color: var(--text-light);
    font-weight: 700; font-size: 17px; letter-spacing: 0.5px;
  }
  /* Front side */
  .card-front .brand-mark {
    position: absolute; right: 48px; top: 70px;
    display: flex; align-items: center; gap: 16px;
    color: var(--brand-blue);
  }
  .card-front .brand-dot { width: 58px; height: 58px; border-width: 6px; }
  .card-front .brand-name { font-size: 38px; }
  .divider {
    position: absolute; left: 40px; right: 40px; top: 190px;
    height: 1px;
    background: linear-gradient(to right, transparent, var(--rule) 40%, var(--rule));
  }
  .office {
    position: absolute; right: 48px; top: 214px; text-align: right;
  }
  .office .office-name { color: var(--brand-blue); font-size: 16px; letter-spacing: 0.5px; }
  .office .office-city { color: var(--text-light); font-size: 17px; margin-top: 2px; }
  .person {
    position: absolute; left: 50px; bottom: 42px;
  }
  .person-name {
    font-family: "Montserrat", Arial, sans-serif;
    font-weight: 600; font-size: 24px; color: var(--brand-blue); letter-spacing: 0.5px;
  }
  .person-role { color: var(--text-light); font-size: 18px; margin-bottom: 18px; }
  .contact-list { list-style: none; }
  .contact-list li {
    display: flex; align-items: center; gap: 10px;
    color: var(--text-light); font-size: 19px; line-height: 1.3;
  }
  .contact-list svg { width: 15px; height: 15px; fill: var(--brand-blue); flex: none; }
</style>
</head>
<body>
<main class="stage">
  <section class="card card-back" aria-label="Card back">
    <div class="brand-mark">
      <span class="brand-dot" aria-hidden="true"></span>
      <span class="brand-name">TalkHarbor</span>
    </div>
    <p class="site">www.TalkHarbor.co.uk</p>
  </section>

  <section class="card card-front" aria-label="Card front">
    <div class="brand-mark">
      <span class="brand-dot" aria-hidden="true"></span>
      <span class="brand-name">TALKHARBOR</span>
    </div>
    <div class="divider"></div>
    <div class="office">
      <p class="office-name">TALKHARBOR</p>
      <p class="office-city">London, UK</p>
    </div>
    <div class="person">
      <p class="person-name">MARCUS HALE</p>
      <p class="person-role">Managing Director</p>
      <ul class="contact-list">
        <li>
          <svg viewBox="0 0 16 16" aria-hidden="true"><path d="M3 1h3l1.5 4-2 1.2a9 9 0 0 0 4.3 4.3L11 8.5 15 10v3a2 2 0 0 1-2 2A12 12 0 0 1 1 3a2 2 0 0 1 2-2z"/></svg>
          044 555 0182
        </li>
        <li>
          <svg viewBox="0 0 16 16" aria-hidden="true"><path d="M1 3h14v10H1z M1 3l7 6 7-6" stroke="#1c1c1e" stroke-width="1.2"/></svg>
          DaniaKV@talkharbor.co.uk
        </li>
        <li>
          <svg viewBox="0 0 16 16" aria-hidden="true"><circle cx="8" cy="8" r="7"/><path d="M1 8h14M8 1c-3 3-3 11 0 14M8 1c3 3 3 11 0 14" stroke="#1c1c1e" stroke-width="1" fill="none"/></svg>
          www.TalkHarbor.co.uk
        </li>
      </ul>
    </div>
  </section>
</main>
</body>
</html>
```